Classy, Elegant, Simple Business Card Design

Looking to have a classy, simple, and elegant design. Want a top notch designed business card. I really like the look of the new torvane credit card. I also like the design I attached. I am trying to reach 21-29 year old females for booking us for there wedding or event. We offer Disc Jockey Service, Photo Booth Rentals, and Uplighting .

Target Market(s)

21-28 year old females

Contact Information for Business Card

Has to have logo, website, email, and phone number

Font styles to use
Other font styles liked:
• open to font choice, modern, clean
Designer to choose
33a6d7
0791cd
0555a3
ffffff

Requirements
Must have
• Has to have logo, website, email, and phone number
Nice to have
• I really like the design of the new torvane credit card. I also included my logo and some designs I like
Should not have
• clutter or too much info

```html
<!DOCTYPE html>
<html lang="en">
<head>
<meta charset="utf-8">
<title>Tidecrest Event Group – Business Card</title>
<link rel="stylesheet" href="https://fonts.googleapis.com/css2?family=Work+Sans:wght@400;500;600&display=swap">
<style>
  :root {
    --bg: #c9e6de;
    --navy: #12305a;
    --ink: #2d3a48;
    --blue: #0791cd;
    --blue-deep: #0555a3;
    --blue-soft: #33a6d7;
    --white: #ffffff;
    --rule: #9cc6e6;
  }
  * { box-sizing: border-box; margin: 0; padding: 0; }
  html, body { width: 1200px; height: 856px; overflow: hidden; }
  body {
    background: var(--bg);
    font-family: "Work Sans", Arial, sans-serif;
    display: flex;
    flex-direction: column;
    align-items: center;
    justify-content: center;
    gap: 40px;
  }
  .card {
    width: 560px;
    height: 320px;
    border-radius: 30px;
    position: relative;
    overflow: hidden;
    box-shadow: 0 6px 18px rgba(20, 60, 70, 0.18);
  }

  /* Front */
  .card--front { background: var(--white); color: var(--ink); }
  .brand {
    position: absolute;
    display: flex;
    align-items: center;
    gap: 10px;
  }
  .brand__dot {
    width: 14px; height: 14px;
    border-radius: 50%;
    background: var(--blue);
    flex: none;
  }
  .brand__name {
    font-weight: 600;
    font-size: 20px;
    letter-spacing: 0.12em;
    color: var(--blue-deep);
    line-height: 1.15;
  }
  .card--front .brand { top: 58px; right: 40px; }
  .front__rule {
    position: absolute;
    left: 80px; right: 40px; top: 128px;
    height: 1px;
    background: var(--rule);
  }
  .person {
    position: absolute;
    left: 44px; top: 150px;
    padding-left: 18px;
    border-left: 5px solid var(--navy);
  }
  .person__name {
    font-weight: 600;
    font-size: 22px;
    color: var(--blue-deep);
    letter-spacing: 0.02em;
  }
  .person__role { font-size: 14px; margin-top: 2px; }
  .address {
    position: absolute;
    left: 67px; top: 212px;
    font-size: 13.5px;
    line-height: 1.35;
  }
  .contacts {
    position: absolute;
    left: 67px; top: 258px;
    list-style: none;
    font-size: 13.5px;
    line-height: 1.35;
  }
  .contacts li { display: flex; align-items: center; gap: 8px; }
  .contacts svg { width: 11px; height: 11px; fill: var(--blue-deep); flex: none; }
  .contacts .accent { color: var(--blue); }

  /* Back */
  .card--back { background: var(--navy); }
  .card--back .brand {
    top: 50%; left: 50%;
    transform: translate(-50%, -60%);
  }
  .card--back .brand__name { color: var(--white); font-size: 24px; }
  .card--back .brand__dot { background: var(--blue-soft); }
  .back__web {
    position: absolute;
    right: 64px; bottom: 36px;
    color: var(--white);
    font-size: 13px;
    letter-spacing: 0.18em;
  }
</style>
</head>
<body>

  <section class="card card--back" aria-label="Card back">
    <div class="brand">
      <span class="brand__dot"></span>
      <span class="brand__name">TIDECREST<br>EVENT GROUP</span>
    </div>
    <p class="back__web">www.tidecrest.com</p>
  </section>

  <section class="card card--front" aria-label="Card front">
    <div class="brand">
      <span class="brand__dot"></span>
      <span class="brand__name">TIDECREST<br>EVENT GROUP</span>
    </div>
    <div class="front__rule"></div>

    <div class="person">
      <p class="person__name">DANIEL REYES</p>
      <p class="person__role">Managing Partner</p>
    </div>

    <p class="address">418 W Harbor Ave.,<br>Rivermont, CA 90210</p>

    <ul class="contacts">
      <li>
        <svg viewBox="0 0 12 12" aria-hidden="true"><path d="M2.5 0.8l2 2-1.1 1.5c.7 1.6 1.7 2.6 3.3 3.3L8.2 6.5l2 2-1 2.2C5 10.5 1.5 7 .8 2.3z"/></svg>
        555-204-7316
      </li>
      <li>
        <svg viewBox="0 0 12 12" aria-hidden="true"><path d="M1 2.5h10v7H1z M1.5 3l4.5 3.5L10.5 3" fill="none" stroke="#0555a3" stroke-width="1.2"/></svg>
        info@tidecrest.com
      </li>
      <li>
        <svg viewBox="0 0 12 12" aria-hidden="true"><circle cx="6" cy="6" r="5" fill="none" stroke="#0555a3" stroke-width="1.2"/><path d="M1 6h10M6 1c-2.5 3-2.5 7 0 10M6 1c2.5 3 2.5 7 0 10" fill="none" stroke="#0555a3" stroke-width="1"/></svg>
        www.<span class="accent">tidecrest</span>.com
      </li>
    </ul>
  </section>

</body>
</html>
```